Redesign Craft Brewing Recipe Website

Originally built with Bootstrap just to get the site going, I am seeking a complete redesign of the sites home page and recipe page. I am an experienced web developer with no graphic background, initially just looking for psd mocks.

I prefer styles that are clean and modern, and would prefer anything that is fun, engaging, and has an organic feel to it. I currently have a cartoon rabbit as a logo, but it needs some modification/tweaking, so any help in that area would be great as well.

Current site:
http://velvetfinch.cloudpagehost.net/

Current launch page/logo:
http://www.velvetfinch.com/

I like the overall layout of the elements currently, but the design sucks.

The launch page is at the following URL

Reason: Still looking for a more modern design. Designs received so far are too similar to the original.

My site is content based and does not contain images or products. Your design should not consist of large images.

Reason: The website has very little images, so the designs need to be more text and content based. The header needs to be very small and should not contain an ad rotater.

Target Market(s)

Home brewers, Craft brewers, Microbreweries, Brewpubs

Requirements
Must have
• Web 2.0 Look and Feel, Fun, Hip, Focus on content
Should not have
• A large photo as a header

```html
<!DOCTYPE html>
<html lang="en">
<head>
<meta charset="utf-8">
<title>Velvetfinch – Recent Recipes</title>
<link rel="stylesheet" href="https://fonts.googleapis.com/css2?family=Ubuntu:wght@400;500;700&display=swap">
<style>
:root{
  --red:#ff0000;
  --orange:#f7821b;
  --grey-tag:#878787;
  --page:#f4f4f4;
  --card:#efefef;
  --card-border:#d9d9d9;
  --text:#222;
  --muted:#5c5c5c;
  --footer:#222;
  --dark-cell:#4a4a4a;
}
*{margin:0;padding:0;box-sizing:border-box}
html,body{width:1200px;height:986px;overflow:hidden}
body{position:relative;background:var(--page);font-family:"Ubuntu",sans-serif;color:var(--text)}
.header{position:absolute;left:0;top:0;width:1200px;height:127px;background:linear-gradient(#f0f0f0,#e3e3e3)}
.brand{position:absolute;left:121px;top:0;width:161px;height:157px;background:#fff;
  clip-path:polygon(0 0,100% 0,100% 142px,50% 157px,0 142px);box-shadow:0 0 4px rgba(0,0,0,.2)}
.brand-wrap{position:absolute;left:120px;top:0;width:163px;height:158px;background:#d8d8d8;
  clip-path:polygon(0 0,100% 0,100% 142px,50% 158px,0 142px)}
.brand-mark{position:absolute;left:56px;top:22px;width:48px;height:48px;border-radius:50%;background:#ececec}
.brand-name{position:absolute;left:0;width:161px;top:92px;text-align:center;font-weight:700;font-size:21px;color:var(--red)}
.nav{position:absolute;top:53px;left:517px;display:flex;list-style:none}
.nav li{height:30px;line-height:30px;font-size:13px;color:#666;font-weight:500;text-transform:uppercase}
.nav .active{background:var(--red);color:#fff;border-radius:4px;width:74px;text-align:center}
.nav li:nth-child(2){margin-left:41px}
.nav li:nth-child(3){margin-left:60px}
.nav li:nth-child(4){margin-left:59px}
.nav li:nth-child(5){margin-left:59px}

.sidebar{position:absolute;left:121px;top:170px;width:199px;height:700px;
  background:linear-gradient(90deg,rgba(0,0,0,0) 170px,rgba(0,0,0,.05) 199px)}
.search{position:absolute;left:0;top:17px;width:182px;height:26px;border:1px solid #c9c9c9;border-radius:3px;background:#fff;
  font-size:13px;color:#999;padding:5px 16px}
.search svg{position:absolute;right:9px;top:6px}
.filter{position:absolute;left:7px}
.filter h3{font-weight:400;font-size:17px;color:#333;margin-bottom:9px}
.filter li{list-style:none;font-size:13px;color:#555;height:22px;display:flex;align-items:center}
.filter li::before{content:"";width:10px;height:10px;border-radius:50%;border:1px solid #aaa;background:linear-gradient(#fff,#ddd);margin-right:10px}
.filter li.checked::before{background:radial-gradient(#222 35%,#eee 45%)}
.divider{position:absolute;left:22px;width:145px;height:1px;background:linear-gradient(90deg,transparent,#ccc,transparent)}
.scrollbar{position:absolute;left:187px;top:94px;width:10px;height:168px;border:1px solid #bbb;border-radius:5px;background:linear-gradient(90deg,#e6e6e6,#cfcfcf)}

.tabs{position:absolute;left:329px;top:184px;width:745px;height:30px}
.tab{position:absolute;top:0;height:30px;line-height:30px;font-size:16px}
.tab.active{left:0;width:134px;background:var(--red);color:#fff;border-radius:4px;text-align:center}
.tab.plain{left:148px;color:#666}
.tabs .rule{position:absolute;left:280px;right:0;top:19px;height:1px;background:#bbb}

.card{position:absolute;width:361px;height:195px;background:var(--card);border:1px solid var(--card-border)}
.card h2{position:absolute;left:15px;top:12px;font-size:15px;font-weight:500;color:#111}
.card .desc{position:absolute;left:15px;top:42px;width:330px;font-size:11.5px;line-height:14px;color:var(--muted)}
.card .author{position:absolute;left:15px;top:83px;font-size:11.5px;color:var(--muted)}
.card .author span{color:var(--red)}
.tag{position:absolute;top:113px;height:24px;line-height:24px;font-size:12px;font-weight:500;color:#fff;border-radius:2px;padding:0 8px}
.tag.method{left:15px}
.tag.style{left:111px;background:var(--grey-tag)}
.tag.orange{background:var(--orange)}
.tag.red{background:var(--red)}
.tag.wide{width:84px;text-align:center}
.stats{position:absolute;right:-1px;bottom:-1px;display:flex}
.stat{width:50px;height:39px;margin-left:1px;background:#fff;border:1px solid #ddd;font-size:11px;color:#555;text-align:center;line-height:14px;padding-top:4px}
.stat.srm{color:#fff;border:none}
.stat.dark{background:var(--dark-cell)}
.stat.orange{background:var(--orange)}

.footer{position:absolute;left:0;top:930px;width:1200px;height:56px;background:var(--footer);color:#ddd;font-size:12px}
.footer a{position:absolute;top:20px;color:#ddd;text-decoration:none}
.footer .sep{position:absolute;left:258px;top:20px}
.footer .copy{position:absolute;right:143px;top:20px}
</style>
</head>
<body>
<header class="header">
  <div class="brand-wrap"></div>
  <div class="brand">
    <div class="brand-mark"></div>
    <div class="brand-name">VELVETFINCH</div>
  </div>
  <ul class="nav">
    <li class="active">Home</li><li>About us</li><li>Recipies</li><li>Company</li><li>Contact us</li>
  </ul>
</header>

<aside class="sidebar">
  <div class="search">Search
    <svg width="12" height="12" viewBox="0 0 12 12"><circle cx="4.5" cy="4.5" r="3.3" fill="none" stroke="#222" stroke-width="1.6"/><line x1="7" y1="7" x2="11" y2="11" stroke="#222" stroke-width="2"/></svg>
  </div>
  <div class="scrollbar"></div>
  <div class="filter" style="top:62px"><h3>BREWING</h3>
    <ul><li>Extract</li><li>Partial Mash</li><li class="checked">All Grain</li></ul></div>
  <div class="divider" style="top:180px"></div>
  <div class="filter" style="top:200px"><h3>STYLES</h3>
    <ul><li>American Amber Ale</li><li>American Barleywine</li><li>American Brown Ale</li><li>American IPA</li><li>American Pale Ale</li><li>American Stout</li><li>American Wheat or Beer</li><li>Applewine</li></ul></div>
  <div class="divider" style="top:431px"></div>
  <div class="filter" style="top:451px"><h3>MATCH MAKER</h3>
    <ul><li>Boil Size</li></ul></div>
</aside>

<div class="tabs">
  <div class="tab active">Recent Recipies</div>
  <div class="tab plain">Popular Recipies</div>
  <div class="rule"></div>
</div>

<main>
  <article class="card" style="left:331px;top:238px">
    <h2>VENOM BELGIAN SPECIALITY ALE</h2>
    <p class="desc">Lorem Ipsum is simply dummy text of the printing and types typesetting industry.</p>
    <p class="author">created by <span>Daniel Marsh</span></p>
    <span class="tag method orange">Partial Mash</span><span class="tag style">Belgian Speciality Ale</span>
    <div class="stats"><div class="stat">13.93%<br>abv</div><div class="stat">126<br>ibu</div><div class="stat">1.036<br>fg</div><div class="stat">1.139<br>og</div><div class="stat srm dark"></div></div>
  </article>
  <article class="card" style="left:712px;top:238px">
    <h2>OAK BASTARD AMERICAN IPA</h2>
    <p class="desc">Lorem Ipsum is simply dummy text of the printing and types typesetting industry.</p>
    <p class="author">created by <span>Daniel Marsh</span></p>
    <span class="tag method red">Partial Mash</span><span class="tag style">Belgian Speciality Ale</span>
    <div class="stats"><div class="stat">13.93%<br>abv</div><div class="stat">126<br>ibu</div><div class="stat">1.036<br>fg</div><div class="stat">1.139<br>og</div><div class="stat srm orange">14<br>srm</div></div>
  </article>
  <article class="card" style="left:331px;top:459px">
    <h2>VENOM ENGLISH CIDER</h2>
    <p class="desc">Lorem Ipsum is simply dummy text of the printing and types typesetting industry.</p>
    <p class="author">created by <span>Daniel Marsh</span></p>
    <span class="tag method orange">Partial Mash</span><span class="tag style">English Cider</span>
    <div class="stats"><div class="stat">13.93%<br>abv</div><div class="stat">126<br>ibu</div><div class="stat">1.036<br>fg</div><div class="stat">1.139<br>og</div><div class="stat srm orange">4<br>srm</div></div>
  </article>
  <article class="card" style="left:712px;top:459px">
    <h2>MOON MAN BLONDE ALE</h2>
    <p class="desc">Lorem Ipsum is simply dummy text of the printing and types typesetting industry.</p>
    <p class="author">created by <span>Daniel Marsh</span></p>
    <span class="tag method red wide">All Grain</span><span class="tag style">Blonde Ale</span>
    <div class="stats"><div class="stat">13.93%<br>abv</div><div class="stat">126<br>ibu</div><div class="stat">1.036<br>fg</div><div class="stat">1.139<br>og</div><div class="stat srm dark">4<br>srm</div></div>
  </article>
  <article class="card" style="left:331px;top:680px">
    <h2>VENOM BELGIAN SPECIALITY ALE</h2>
    <p class="desc">Lorem Ipsum is simply dummy text of the printing and types typesetting industry.</p>
    <p class="author">created by <span>Daniel Marsh</span></p>
    <span class="tag method orange">Partial Mash</span><span class="tag style">Belgian Speciality Ale</span>
    <div class="stats"><div class="stat">13.93%<br>abv</div><div class="stat">126<br>ibu</div><div class="stat">1.036<br>fg</div><div class="stat">1.139<br>og</div><div class="stat srm dark"></div></div>
  </article>
  <article class="card" style="left:712px;top:680px">
    <h2>VENOM BELGIAN SPECIALITY ALE</h2>
    <p class="desc">Lorem Ipsum is simply dummy text of the printing and types typesetting industry.</p>
    <p class="author">created by <span>Daniel Marsh</span></p>
    <span class="tag method red">Partial Mash</span><span class="tag style">Belgian Speciality Ale</span>
    <div class="stats"><div class="stat">13.93%<br>abv</div><div class="stat">126<br>ibu</div><div class="stat">1.036<br>fg</div><div class="stat">1.139<br>og</div><div class="stat srm dark"></div></div>
  </article>
</main>

<footer class="footer">
  <a href="#" style="left:136px">Terms of Service</a>
  <span class="sep">|</span>
  <a href="#" style="left:297px">Contact</a>
  <span class="copy">Copyright © 2013 Velvetfinch. All rights reserved.</span>
</footer>
</body>
</html>
```